Business Card Re-Design/Update

We'd like to update out business cards. I've included our current "Style guide" which has the colour scheme of the organisation in it. I've also included the branding files with logos etc in them.

I've also included a copy of one of our existing cards so that you can see how ugly/dated they look. I'd like a fresh modern corporate look.

Target Market(s)

These are for our clients, potential clients, industry contacts - like all business cards

Contact Information for Business Card

Name
Position
Company Address - Level 1, 47 Fernby Street, Carlow Qld 4072
Direct Phone
mobile
Email
Website -www.korvalit.com.au
Logo

Colors

Designer to choose colors to be used in the design.

Requirements
Must have
• Main Logo
• Cards will need to be editable to be able to personalize them for each new employee.
Nice to have
• The MapOut, ShipWell, KeepSteady would be okay to have if they can be sensibly and professionally added to the look without detracting from the main imagery.
• Maybe they could go on the back of the card? will leave this to your creative discretion as to whether/where they fit.
Should not have
• Should not have decorative or script fonts

```html
<!DOCTYPE html>
<html lang="en">
<head>
<meta charset="utf-8">
<title>korvalIT business card</title>
<link rel="stylesheet" href="https://fonts.googleapis.com/css2?family=Roboto:wght@400;500;700&family=Roboto+Condensed:wght@400;700&display=swap">
<style>
  :root {
    --red: #c8141d;
    --red-deep: #a90d16;
    --white: #ffffff;
    --paper: #f4f4f4;
    --ink: #2b2b2b;
    --bg: #2f2f2f;
    --green: #6aa83a;
    --blue: #1f8fd6;
    --magenta: #b5238f;
    --grey-rule: #9a9a9a;
  }
  * { margin: 0; padding: 0; box-sizing: border-box; }
  html, body { width: 1200px; height: 911px; overflow: hidden; }
  body {
    background: var(--bg);
    font-family: "Roboto", Arial, sans-serif;
    position: relative;
  }
  .card {
    position: absolute;
    width: 620px;
    height: 354px;
    left: 290px;
    box-shadow: 0 8px 24px rgba(0,0,0,.45);
    overflow: hidden;
  }
  .card-front {
    top: 70px;
    background: linear-gradient(135deg, var(--red) 0%, var(--red-deep) 100%);
    color: var(--white);
  }
  .card-back {
    top: 470px;
    background: var(--paper);
  }
  .name-band {
    position: absolute;
    left: 0; right: 0;
    top: 44px;
    height: 84px;
    background: var(--white);
    display: flex;
    align-items: center;
    justify-content: space-between;
    padding: 0 34px 0 34px;
  }
  .person-name {
    font-family: "Roboto Condensed", Arial, sans-serif;
    font-weight: 700;
    font-size: 24px;
    color: var(--red);
    letter-spacing: .3px;
    line-height: 1.1;
  }
  .person-title {
    font-family: "Roboto Condensed", Arial, sans-serif;
    font-size: 15px;
    color: var(--ink);
    margin-top: 2px;
  }
  .brand {
    display: flex;
    align-items: center;
    gap: 10px;
  }
  .brand-square {
    width: 30px; height: 30px;
    background: var(--red);
  }
  .brand-name {
    font-weight: 500;
    font-size: 40px;
    color: var(--ink);
    letter-spacing: -0.5px;
  }
  .contact-list {
    position: absolute;
    right: 34px;
    top: 160px;
    list-style: none;
    font-size: 14px;
    line-height: 20px;
  }
  .contact-list li { display: flex; align-items: center; gap: 8px; }
  .contact-list svg { width: 12px; height: 12px; flex: none; }
  .address {
    position: absolute;
    left: 34px;
    bottom: 30px;
    font-size: 14px;
    line-height: 19px;
    font-style: normal;
  }
  .back-brand {
    position: absolute;
    left: 0; right: 0;
    top: 120px;
    text-align: center;
    font-weight: 700;
    font-size: 56px;
    color: var(--red);
    letter-spacing: -1px;
  }
  .service-row {
    position: absolute;
    left: 0; right: 0;
    bottom: 40px;
    display: flex;
    justify-content: center;
    align-items: center;
    gap: 18px;
    font-size: 22px;
    font-weight: 500;
  }
  .service-rule { width: 1px; height: 22px; background: var(--grey-rule); }
  .service-map { color: var(--green); }
  .service-ship { color: var(--blue); }
  .service-keep { color: var(--magenta); }
</style>
</head>
<body>

<section class="card card-front" aria-label="Card front">
  <div class="name-band">
    <div class="person">
      <div class="person-name">MAREN HOLT</div>
      <div class="person-title">Business Development Manager</div>
    </div>
    <div class="brand">
      <span class="brand-square"></span>
      <span class="brand-name">korvalIT</span>
    </div>
  </div>

  <ul class="contact-list">
    <li><svg viewBox="0 0 12 12"><path d="M3 1l2 2-1 1.5a7 7 0 0 0 3.5 3.5L9 7l2 2-1.5 2C5 10.5 1.5 7 1 2.5z" fill="#fff"/></svg>+61 (0)7 3480 2214</li>
    <li><svg viewBox="0 0 12 12"><path d="M3 1l2 2-1 1.5a7 7 0 0 0 3.5 3.5L9 7l2 2-1.5 2C5 10.5 1.5 7 1 2.5z" fill="#fff"/></svg>+61 (0)7 3480 2267</li>
    <li><svg viewBox="0 0 12 12"><rect x="3" y="0.5" width="6" height="11" rx="1" fill="none" stroke="#fff"/></svg>+61 (0)412 905 318</li>
    <li><svg viewBox="0 0 12 12"><rect x="1" y="4" width="10" height="6" fill="#fff"/><rect x="3" y="1" width="6" height="3" fill="none" stroke="#fff"/></svg>+61 (0)7 3480 2290</li>
    <li><svg viewBox="0 0 12 12"><rect x="0.5" y="2" width="11" height="8" fill="#fff"/><path d="M0.5 2l5.5 4.5L11.5 2" fill="none" stroke="#c8141d"/></svg>mholt@korvalit.com.au</li>
  </ul>

  <address class="address">
    Level 1, 47 Fernby Street<br>
    Carlow Qld 4072<br>
    www.korvalit.com.au
  </address>
</section>

<section class="card card-back" aria-label="Card back">
  <div class="back-brand">korvalIT</div>
  <div class="service-row">
    <span class="service-map">MapOut</span>
    <span class="service-rule"></span>
    <span class="service-ship">ShipWell</span>
    <span class="service-rule"></span>
    <span class="service-keep">KeepSteady</span>
  </div>
</section>

</body>
</html>
```